Exciting opportunity to create logo and a label for our natural health brand.

About us

We are a customer centric health supplement brand who believes in natural medicine and high quality ingredients. We take a holistic approach to healthcare, with an eastern philosophy. We believe in being partners with our customers in their health care journey and are invested in their well being.

Our brand philosophy and values are attached (see Vorna philosophy.png). Our personality traits are:

- Natural
- Fresh
- Modern
- Balanced (in a holistic sense)

Task breakdown

1. Design a fresh feeling logo for us
- We want it to represent our values and high quality ingredients. We would like the quality of the product to be reflected in the branding and have a high end feel.
- Logo text must include Vorna Health Sciences
- We want the Vorna to be the focus of the logo (see uploaded image Vorna logo example.png)
The logo does not have to follow this layout, but we just want the Vorna to stand out. Feel free to use your creative license on this!

2. Create an attractive label to go on the supplement bottle
- The designs need to be eye catching, give a sense of high end ingredients and natural products and tie in with the logo to give a joined up feel.
- We are selling our products online and need them to really stand out from the competition.
- See examples of labels and packaging we like (1 -7 label design).

The initial label we would like you to design would be for our product Calm Drift. It is a product that assists in the management of Anxiety and stress. The label will appear on the bottle that holds the capsules for this supplement, see uploaded files (Example plain bottles.png). The bottles may be white as the picture shows or dark blue recyclable plastic or dark brown glass . We don't have the exact dimensions of the bottle yet, but I will follow up with these.

The label needs to include the following things:
1. The logo
2. The name of the product
3. The product is to help with the relief of Anxiety and Stress
4. Number of capsules the bottle contains
5. The back of the label should have
i) The ingredients
ii) Dosage
iii) Directions of use

Please use placeholder text where needed.

We look forward to seeing your design. Thank you.

```html
<!DOCTYPE html>
<html lang="en">
<head>
<meta charset="UTF-8">
<title>Vorna Health Science — Calm Drift label</title>
<link href="https://fonts.googleapis.com/css2?family=Barlow:wght@500;600&display=swap" rel="stylesheet">
<style>
  :root {
    --page: #f3f4f4;
    --label-green: #04735f;
    --band-teal: #186a70;
    --botanical: #0d8068;
    --ink-light: #ffffff;
  }
  * { margin: 0; padding: 0; box-sizing: border-box; }
  html, body {
    width: 1200px;
    height: 750px;
    overflow: hidden;
    background: var(--page);
  }
  .canvas {
    position: relative;
    width: 1200px;
    height: 750px;
    display: flex;
    align-items: center;
    justify-content: center;
  }
  .label {
    position: relative;
    width: 562px;
    height: 700px;
    background: var(--label-green);
    overflow: hidden;
    font-family: "Barlow", "DIN Alternate", Arial, sans-serif;
    color: var(--ink-light);
  }
  .botanical {
    position: absolute;
    right: 0;
    width: 340px;
    background: radial-gradient(ellipse at 70% 50%, var(--botanical) 0%, rgba(13,128,104,0.35) 55%, rgba(4,115,95,0) 80%);
    opacity: 0.8;
  }
  .botanical--upper { top: 20px; height: 300px; }
  .botanical--lower { bottom: 0; height: 250px; }
  .brand {
    position: absolute;
    top: 96px;
    left: 0;
    right: 0;
    text-align: center;
  }
  .brand__name {
    font-size: 112px;
    font-weight: 500;
    line-height: 1;
    letter-spacing: 1px;
  }
  .brand__descriptor {
    margin-top: 26px;
    font-size: 16px;
    font-weight: 500;
    letter-spacing: 12px;
    padding-left: 12px;
  }
  .product-band {
    position: absolute;
    top: 326px;
    left: 0;
    right: 0;
    height: 130px;
    background: var(--band-teal);
    box-shadow: 0 -3px 6px rgba(0,0,0,0.12), 0 3px 6px rgba(0,0,0,0.12);
    text-align: center;
    padding-top: 30px;
  }
  .product-band__name {
    font-size: 38px;
    font-weight: 600;
    line-height: 1;
    letter-spacing: 0.5px;
  }
  .product-band__claim {
    margin-top: 10px;
    font-size: 21px;
    font-weight: 500;
    letter-spacing: 1.6px;
  }
  .capsule-count {
    position: absolute;
    top: 596px;
    left: 0;
    right: 0;
    text-align: center;
    line-height: 1;
  }
  .capsule-count__number {
    font-size: 32px;
    font-weight: 600;
    letter-spacing: 1px;
  }
  .capsule-count__unit {
    margin-top: 4px;
    font-size: 25px;
    font-weight: 500;
    letter-spacing: 2px;
  }
</style>
</head>
<body>
  <main class="canvas">
    <section class="label">
      <div class="botanical botanical--upper" role="img" aria-label="Faint line-drawn botanical sprigs with leaves and blossoms"></div>
      <div class="botanical botanical--lower" role="img" aria-label="Faint line-drawn botanical stems with leaves"></div>

      <header class="brand">
        <div class="brand__name">Vorna</div>
        <div class="brand__descriptor">HEALTH SCIENCE</div>
      </header>

      <div class="product-band">
        <h1 class="product-band__name">Calm Drift</h1>
        <p class="product-band__claim">Reduce stress and anxiety naturally</p>
      </div>

      <div class="capsule-count">
        <div class="capsule-count__number">60</div>
        <div class="capsule-count__unit">capsules</div>
      </div>
    </section>
  </main>
</body>
</html>
```